Detail Shop Business card design

i need a business card design for my new detailing company called 'Brisk's Polish Works'. i want an all black and white design . simple, direct and to the point. i want the designer to choose a fitting font to match the logothe front should have logo, address, phone and email and the back side should have a slogan and text indicating that we offer services on anything including cars, trucks, motorcycles and RVs. slogan will read "we take pride in your ride"
maybe also very small on the back side the IG icon with Brisks_Polish_Works

phone 208.417.6352
address 3847 E Larkin Ave
Spokane WA 99214
email: BrisksPolish@mailvexo.com

Target Market(s)

all ages , auto enthusiasts

Industry/Entity Type

Automotive

Contact Information for Business Card

the front should have logo, address, phone and email and the back side should have a slogan and text indicating that we offer services on anything including cars, trucks, motorcycles and RVs. slogan will read "we take pride in your ride"

phone 208.417.6352
address 3847 E Larkin Ave
Spokane WA 99214

Colors
000000
ffffff

Requirements
Must have
• bold font and very simple design with good spacing
Nice to have
• anything creative from the designer indicating we service any types of vehicles
Should not have
• any colors ,

```html
<!DOCTYPE html>
<html lang="en">
<head>
<meta charset="UTF-8">
<title>Brisk's Polish Works – Business Cards</title>
<link rel="stylesheet" href="https://fonts.googleapis.com/css2?family=Roboto+Slab:wght@400;500;700&display=swap">
<style>
  :root {
    --stage: #1f1f20;
    --card: #141414;
    --ink: #ffffff;
    --ink-soft: #d9d9d9;
  }
  * { margin: 0; padding: 0; box-sizing: border-box; }
  html, body {
    width: 1200px;
    height: 900px;
    overflow: hidden;
    background: var(--stage);
    font-family: "Roboto Slab", Georgia, serif;
    color: var(--ink);
  }
  .stage {
    position: relative;
    width: 1200px;
    height: 900px;
  }
  .card {
    position: absolute;
    left: 260px;
    width: 680px;
    height: 389px;
    background: var(--card);
    box-shadow: 0 10px 30px rgba(0,0,0,0.45);
  }
  .card--back { top: 50px; }
  .card--front { top: 470px; }

  /* Back side */
  .brand-mark {
    display: flex;
    align-items: center;
    justify-content: center;
    gap: 14px;
  }
  .brand-mark__dot {
    width: 22px;
    height: 22px;
    border-radius: 50%;
    background: var(--ink);
  }
  .brand-mark__name {
    font-weight: 700;
    color: var(--ink);
    letter-spacing: 0.02em;
  }
  .card--back .brand-mark {
    position: absolute;
    top: 120px;
    left: 0;
    right: 0;
  }
  .card--back .brand-mark__name { font-size: 38px; }
  .slogan {
    position: absolute;
    top: 250px;
    left: 0;
    right: 0;
    display: flex;
    align-items: center;
    justify-content: center;
    gap: 14px;
    font-size: 17px;
    letter-spacing: 0.12em;
    text-transform: uppercase;
  }
  .slogan__rule {
    width: 56px;
    height: 1px;
    background: var(--ink);
  }
  .vehicles {
    position: absolute;
    top: 290px;
    left: 0;
    right: 0;
    text-align: center;
    font-size: 17px;
    letter-spacing: 0.1em;
    text-transform: uppercase;
  }

  /* Front side */
  .person {
    position: absolute;
    top: 50px;
    left: 60px;
  }
  .person__name {
    font-size: 27px;
    font-weight: 500;
    letter-spacing: 0.05em;
    text-transform: uppercase;
  }
  .person__role {
    font-size: 15px;
    color: var(--ink-soft);
  }
  .address {
    position: absolute;
    top: 150px;
    left: 60px;
    font-size: 18px;
    line-height: 1.3;
  }
  .contacts {
    position: absolute;
    top: 262px;
    left: 60px;
    list-style: none;
    font-size: 18px;
    line-height: 1.4;
  }
  .contacts li {
    display: flex;
    align-items: center;
    gap: 10px;
  }
  .contacts svg {
    width: 13px;
    height: 13px;
    flex: none;
  }
  .card--front .brand-mark {
    position: absolute;
    top: 150px;
    right: 40px;
    width: 280px;
    flex-direction: column;
    gap: 16px;
    text-align: center;
  }
  .card--front .brand-mark__dot { width: 30px; height: 30px; }
  .card--front .brand-mark__name { font-size: 34px; line-height: 1.15; }
</style>
</head>
<body>
<main class="stage">

  <section class="card card--back" aria-label="Card back">
    <div class="brand-mark">
      <span class="brand-mark__dot"></span>
      <span class="brand-mark__name">Brisk's Polish Works</span>
    </div>
    <p class="slogan">
      <span class="slogan__rule"></span>
      We take pride in your ride
      <span class="slogan__rule"></span>
    </p>
    <p class="vehicles">Cars – Trucks – Motorcycles and RVs</p>
  </section>

  <section class="card card--front" aria-label="Card front">
    <div class="person">
      <h1 class="person__name">Daniel Reyes</h1>
      <p class="person__role">Director</p>
    </div>
    <address class="address">
      3847 E Larkin Ave<br>
      Spokane WA 99214
    </address>
    <ul class="contacts">
      <li>
        <svg viewBox="0 0 16 16" aria-hidden="true"><path fill="#fff" d="M4 1l2.5 3.5-1.5 1.5c.8 1.8 2.3 3.3 4 4l1.5-1.5L14 11l-1.5 3C7 14 2 9 2 3z"/></svg>
        208.417.6352
      </li>
      <li>
        <svg viewBox="0 0 16 16" aria-hidden="true"><rect x="1.5" y="3.5" width="13" height="9" fill="none" stroke="#fff" stroke-width="1.4"/><path d="M1.5 3.5L8 9l6.5-5.5" fill="none" stroke="#fff" stroke-width="1.4"/></svg>
        BrisksPolish@mailvexo.com
      </li>
      <li>
        <svg viewBox="0 0 16 16" aria-hidden="true"><circle cx="8" cy="8" r="6.3" fill="none" stroke="#fff" stroke-width="1.3"/><path d="M1.7 8h12.6M8 1.7c-3 3.5-3 9 0 12.6M8 1.7c3 3.5 3 9 0 12.6" fill="none" stroke="#fff" stroke-width="1.1"/></svg>
        www.BrisksPolish.com
      </li>
    </ul>
    <div class="brand-mark">
      <span class="brand-mark__dot"></span>
      <span class="brand-mark__name">Brisk's Polish Works</span>
    </div>
  </section>

</main>
</body>
</html>
```